website design for M&T Electric

A portfolio website for a high end commercial and residential electrical contracting company. The current site mandtelectric.example does not represent the current direction but the images in the gallery give you an idea of the work we do. Current logo will be uploaded shortly but is black text on white background.
Target Market(s)
General Contractors, Residential Home Owners, clients intersted in Velmora home automation.
Industry/Entity Type
Electrician
Coding
Coded - Design and coding required
Number of Pages Required
2 page
Font styles to use
Sans Serif
Colors
Designer to choose colors to be used in the design.
Requirements
Must have
- Portfolio section highlighting different service areas and products (Velmora Housepilot, etc)

```html
<!DOCTYPE html>
<html lang="en">
<head>
<meta charset="utf-8">
<title>M&amp;T Electric</title>
<link href="https://fonts.googleapis.com/css2?family=Open+Sans:ital,wght@0,400;0,600;0,700;0,800;1,400&family=Roboto:wght@300;400;500;700&display=swap" rel="stylesheet">
<style>
:root{
  --navy:#1c2b50;
  --navy-deep:#17223f;
  --ink:#222;
  --muted:#777;
  --line:#e3e3e3;
  --white:#fff;
  --black-bar:#0f1628;
}
*{box-sizing:border-box;margin:0;padding:0}
html,body{width:1200px;height:3237px;overflow:hidden}
body{position:relative;background:var(--white);font-family:"Open Sans",Arial,sans-serif;color:var(--ink)}
.abs{position:absolute}
.center{text-align:center;left:0;width:1200px}

/* header */
.site-header{position:absolute;left:0;top:0;width:1200px;height:123px;background:linear-gradient(#2b2b2b,#0e0e0e)}
.brand{position:absolute;left:99px;top:38px;font-family:"Roboto",sans-serif;font-weight:300;font-size:44px;color:var(--white);letter-spacing:1px}
.main-nav a{position:absolute;top:60px;font-family:"Roboto",sans-serif;font-size:15px;color:#cfcfcf;text-decoration:none}
.search-icon{position:absolute;left:1085px;top:60px}

/* hero */
.hero{position:absolute;left:0;top:123px;width:1200px;height:544px;background:linear-gradient(180deg,#3d4455 0%,#6b6a70 35%,#8a6d4e 70%,#3a2c22 100%)}
.hero-title{position:absolute;left:120px;width:960px;top:206px;text-align:center;font-family:"Roboto",sans-serif;font-weight:300;font-size:38px;line-height:48px;color:var(--white)}
.hero-arrow{position:absolute;top:224px;width:54px;height:54px;border:2px solid rgba(255,255,255,.85);border-radius:50%}

/* welcome */
.section-title{position:absolute;font-family:"Roboto",sans-serif;font-weight:700;font-size:30px;color:var(--ink);text-align:center;left:0;width:1200px}
.lede{position:absolute;left:190px;width:820px;text-align:center;font-size:12.5px;line-height:27px;color:var(--muted)}
.service-card{position:absolute;top:915px;width:309px;height:250px;border:1px solid var(--line);background:var(--white);text-align:center}
.service-icon{position:absolute;left:90px;top:-66px;width:128px;height:128px;border-radius:50%;background:var(--navy);border:5px solid var(--white);box-shadow:0 0 0 2px #d5d8df}
.service-card h3{position:absolute;top:78px;left:0;width:100%;font-family:"Roboto",sans-serif;font-weight:500;font-size:19px;color:var(--ink)}
.service-card p{position:absolute;top:114px;left:20px;right:20px;font-size:12px;line-height:22px;color:var(--muted)}
.read-more{position:absolute;top:205px;left:0;width:100%;font-family:"Roboto",sans-serif;font-weight:700;font-size:12.5px;color:var(--ink)}

/* about */
.about{position:absolute;left:0;top:1252px;width:1200px;height:373px;background:linear-gradient(180deg,rgba(28,43,80,.92),rgba(28,43,80,.82)),linear-gradient(90deg,#4a5a7a,#7884a0,#3c4a68)}
.about h2{position:absolute;top:46px;left:0;width:1200px;text-align:center;font-family:"Roboto",sans-serif;font-weight:300;font-size:60px;color:var(--white)}
.about p{position:absolute;top:140px;left:170px;width:860px;text-align:center;font-size:14px;line-height:23px;color:#e7e9ef}
.btn-outline{position:absolute;top:247px;left:494px;width:210px;height:50px;border:2px solid var(--white);color:var(--white);font-family:"Roboto",sans-serif;font-size:17px;line-height:46px;text-align:center}

/* gallery */
.tile{position:absolute;width:231px;height:193px;display:flex;align-items:center;justify-content:center;text-align:center;font-weight:800;font-size:27px;line-height:31px;letter-spacing:1.5px;color:var(--white);text-shadow:0 1px 3px rgba(0,0,0,.45)}

/* testimonials */
.testimonials{position:absolute;left:0;top:2249px;width:1200px;height:326px;background:linear-gradient(180deg,rgba(28,43,80,.95),rgba(28,43,80,.9)),#2a3a60}
.testimonials h2{position:absolute;top:60px;left:0;width:1200px;text-align:center;font-family:"Roboto",sans-serif;font-weight:700;font-size:30px;color:var(--white)}
.quote-badge{position:absolute;left:98px;top:115px;width:118px;height:118px;border-radius:50%;background:#e8e9ec}
.avatar{position:absolute;left:170px;top:98px;width:118px;height:118px;border-radius:50%;background:linear-gradient(135deg,#c9c9c9,#6d6d6d);border:4px solid var(--white)}
.quote-text{position:absolute;left:311px;top:124px;width:800px;font-style:italic;font-size:12.5px;line-height:22px;color:#e3e6ee}
.client-name{position:absolute;left:311px;top:202px;font-family:"Roboto",sans-serif;font-weight:500;font-size:13px;color:var(--white)}
.client-city{position:absolute;left:311px;top:226px;font-family:"Roboto",sans-serif;font-size:12px;color:#cfd4e0}
.dot{position:absolute;top:270px;width:10px;height:10px;border-radius:50%;border:2px solid var(--white)}
.dot.on{background:var(--white)}

/* clients */
.client-box{position:absolute;top:2756px;width:154px;height:93px;border:1px solid #dcdcdc;display:flex;align-items:center;justify-content:center;gap:8px;font-family:"Open Sans",sans-serif;font-weight:600;font-size:17px;color:#444}
.client-box i{display:block;width:12px;height:12px;background:#444;border-radius:50%}
.client-arrow{position:absolute;top:2788px}

/* footer */
.site-footer{position:absolute;left:0;top:2905px;width:1200px;height:270px;background:var(--navy)}
.site-footer h4{position:absolute;top:50px;font-family:"Roboto",sans-serif;font-weight:700;font-size:13px;color:var(--white);letter-spacing:.5px}
.footer-list{position:absolute;top:82px;list-style:none}
.footer-list li{font-size:11px;line-height:27px;color:#d4d8e3}
.newsletter-copy{position:absolute;left:252px;top:80px;width:260px;font-size:11px;line-height:20px;color:#d4d8e3}
.email-field{position:absolute;left:252px;top:125px;width:242px;height:39px;background:var(--white);font-size:11px;color:#888;padding:12px 12px}
.btn-subscribe{position:absolute;left:252px;top:181px;width:91px;height:41px;background:#0b1020;color:var(--white);font-family:"Roboto",sans-serif;font-size:12px;line-height:41px;text-align:center}
.vrule{position:absolute;top:50px;width:1px;height:175px;background:rgba(255,255,255,.15)}
.contact-line{position:absolute;left:939px;font-size:11px;line-height:20px;color:#d4d8e3}

.bottom-bar{position:absolute;left:0;top:3175px;width:1200px;height:62px;background:var(--black-bar)}
.bottom-bar .copy{position:absolute;left:99px;top:22px;font-size:11px;color:#c8ccd6}
.bottom-bar .social{position:absolute;right:96px;top:22px;font-size:11px;color:#c8ccd6;display:flex;gap:14px}
.bottom-bar .social b{font-weight:600;color:var(--white)}
</style>
</head>
<body>

<header class="site-header">
  <div class="brand">M&amp;T Electric</div>
  <nav class="main-nav">
    <a style="left:541px">Home</a>
    <a style="left:632px">Gallery</a>
    <a style="left:728px">Specialty Services</a>
    <a style="left:895px">About</a>
    <a style="left:986px">Contact</a>
  </nav>
  <svg class="search-icon" width="16" height="16" viewBox="0 0 16 16"><circle cx="6.5" cy="6.5" r="5" fill="none" stroke="#cfcfcf" stroke-width="2"/><line x1="10" y1="10" x2="15" y2="15" stroke="#cfcfcf" stroke-width="2"/></svg>
</header>

<section class="hero" role="img" aria-label="Photo of a lit modern commercial building at dusk">
  <div class="hero-arrow" style="left:25px"><svg width="50" height="50" viewBox="0 0 50 50"><polyline points="28,18 21,25 28,32" fill="none" stroke="#fff" stroke-width="2.5"/></svg></div>
  <h1 class="hero-title">We are a high end commercial and residential electrical contracting company</h1>
  <div class="hero-arrow" style="left:1128px"><svg width="50" height="50" viewBox="0 0 50 50"><polyline points="22,18 29,25 22,32" fill="none" stroke="#fff" stroke-width="2.5"/></svg></div>
</section>

<h2 class="section-title" style="top:722px">WELCOME TO M&amp;T ELECTRIC</h2>
<p class="lede" style="top:770px">Sed ut perspiciatis unde omnis iste natus error sit voluptatem accusantium doloremque laudantium, totam rem aperiam, eaque ipsa quae ab illo inventore veritatis et quasi architecto beatae vitae dicta sunt explicabo.</p>

<article class="service-card" style="left:99px">
  <div class="service-icon"><svg width="118" height="118" viewBox="0 0 118 118"><rect x="46" y="38" width="26" height="42" fill="#fff"/><g fill="#1c2b50"><rect x="50" y="43" width="4" height="4"/><rect x="57" y="43" width="4" height="4"/><rect x="64" y="43" width="4" height="4"/><rect x="50" y="52" width="4" height="4"/><rect x="57" y="52" width="4" height="4"/><rect x="64" y="52" width="4" height="4"/><rect x="50" y="61" width="4" height="4"/><rect x="64" y="61" width="4" height="4"/><rect x="55" y="70" width="8" height="10"/></g></svg></div>
  <h3>COMMERCIAL</h3>
  <p>Sed ut perspiciatis unde omnis iste natus error sit voluptatem accusantium doloremque laudantium, totam rem aperiam, eaque ipsa quae.</p>
  <div class="read-more">READ MORE &#9654;</div>
</article>
<article class="service-card" style="left:446px">
  <div class="service-icon"><svg width="118" height="118" viewBox="0 0 118 118"><polygon points="59,34 34,56 84,56" fill="#fff"/><rect x="40" y="55" width="38" height="26" fill="#fff"/><rect x="54" y="64" width="10" height="17" fill="#1c2b50"/><rect x="44" y="60" width="7" height="7" fill="#1c2b50"/></svg></div>
  <h3>RESIDENTIAL</h3>
  <p>Sed ut perspiciatis unde omnis iste natus error sit voluptatem accusantium doloremque laudantium, totam rem aperiam, eaque ipsa quae.</p>
  <div class="read-more">READ MORE &#9654;</div>
</article>
<article class="service-card" style="left:792px">
  <div class="service-icon"><svg width="118" height="118" viewBox="0 0 118 118"><g fill="#fff"><rect x="32" y="50" width="14" height="28"/><rect x="48" y="40" width="14" height="38"/><rect x="64" y="46" width="12" height="32"/><rect x="78" y="54" width="10" height="24"/></g><g fill="#1c2b50"><rect x="36" y="55" width="2" height="18"/><rect x="52" y="45" width="2" height="28"/><rect x="56" y="45" width="2" height="28"/><rect x="68" y="51" width="2" height="22"/><rect x="82" y="59" width="2" height="15"/></g></svg></div>
  <h3>LANDSCAPE</h3>
  <p>Sed ut perspiciatis unde omnis iste natus error sit voluptatem accusantium doloremque laudantium, totam rem aperiam, eaque ipsa quae.</p>
  <div class="read-more">READ MORE &#9654;</div>
</article>

<section class="about" role="img" aria-label="Tall building under construction behind a navy overlay">
  <h2>About Us</h2>
  <p>M&amp;T Electric is a full service electrical contracting shop. We offer commercial, residential, light industrial, and agricultural services. We're Velmora Housepilot and Velmora Motorized Shades certified, as well as an authorized Kelvar Power generator dealer. We've served the Wood River and South Central Idaho area for over 18 years.</p>
  <div class="btn-outline">MORE INFORMATION</div>
</section>

<h2 class="section-title" style="top:1673px">OUR GALLERY</h2>
<div class="tile" style="left:99px;top:1759px;background:linear-gradient(160deg,#6d86a8,#6b5744 60%,#4a4d52)" role="img" aria-label="Commercial project photo">COMMERCIAL</div>
<div class="tile" style="left:356px;top:1759px;background:linear-gradient(160deg,#5a3a44,#8a6a70 50%,#4a3a3e)" role="img" aria-label="Residential project photo">RESIDENTIAL</div>
<div class="tile" style="left:613px;top:1759px;background:linear-gradient(180deg,#8b8aa6,#5c5670 55%,#3f3a48)" role="img" aria-label="Landscape lighting project photo">LANDSCAPE</div>
<div class="tile" style="left:870px;top:1759px;background:linear-gradient(160deg,#7e7e7e,#c9c9c9 50%,#6a6a6a)" role="img" aria-label="Generator installation photo">GENERATORS</div>
<div class="tile" style="left:99px;top:1972px;background:linear-gradient(180deg,#8aa6c6,#9d8c74 60%,#6f6a66)" role="img" aria-label="Velmora shades project photo">VELMORA<br>SHADES</div>
<div class="tile" style="left:356px;top:1972px;background:linear-gradient(180deg,#9fb0c4,#6e5a4c 55%,#4d4540)" role="img" aria-label="Velmora dimming project photo">VELMORA<br>DIMMING</div>
<div class="tile" style="left:613px;top:1972px;background:linear-gradient(180deg,#2c2c2c,#4a4640 60%,#262420)" role="img" aria-label="LED lighting fixtures photo">LED<br>LIGHTING</div>
<div class="tile" style="left:870px;top:1972px;background:linear-gradient(160deg,#3a3a3a,#6e625a 55%,#2a2a2a)" role="img" aria-label="Electrician on a service call photo">SERVICE<br>CALLS</div>

<section class="testimonials">
  <h2>CLIENT TESTIMONIALS</h2>
  <div class="quote-badge"><svg width="118" height="118" viewBox="0 0 118 118"><g fill="#c9cbd0"><circle cx="42" cy="64" r="10"/><path d="M34 62 Q36 44 50 40 L50 46 Q42 50 42 58Z"/><circle cx="66" cy="64" r="10"/><path d="M58 62 Q60 44 74 40 L74 46 Q66 50 66 58Z"/></g></svg></div>
  <div class="avatar" role="img" aria-label="Client portrait photo"></div>
  <p class="quote-text">Sed ut perspiciatis unde omnis iste natus error sit voluptatem accusantium doloremque laudantium, totam rem aperiam, eaque ipsa quae ab illo inventore veritatis et quasi architecto beatae vitae dicta sunt explicabo. Nemo enim ipsam voluptatem quia voluptas sit aspernatur aut odit aut fugit, sed quia consequuntur magni dolores eos qui ratione voluptatem sequi nesciunt.</p>
  <div class="client-name">JOHN SMITH</div>
  <div class="client-city">CITY NAME</div>
  <span class="dot" style="left:569px"></span><span class="dot on" style="left:585px"></span><span class="dot" style="left:601px"></span><span class="dot" style="left:617px"></span>
</section>

<h2 class="section-title" style="top:2616px">OUR CLIENTS</h2>
<p class="lede" style="top:2670px">Neque porro quisquam est, qui dolorem ipsum quia dolor sit amet, consectetur, adipisci velit, sed quia non numquam eius modi tempora incidunt ut labore et dolore magnam aliquam quaerat voluptatem.</p>
<svg class="client-arrow" style="left:55px" width="20" height="30" viewBox="0 0 20 30"><polyline points="16,4 5,15 16,26" fill="none" stroke="#aaa" stroke-width="3"/></svg>
<div class="client-box" style="left:99px"><i></i>Norvane</div>
<div class="client-box" style="left:268px">Gridleaf</div>
<div class="client-box" style="left:438px">Hollowell</div>
<div class="client-box" style="left:606px">Brackenfield</div>
<div class="client-box" style="left:777px">Tarsway</div>
<div class="client-box" style="left:945px"><i></i>Quillmark</div>
<svg class="client-arrow" style="left:1127px" width="20" height="30" viewBox="0 0 20 30"><polyline points="4,4 15,15 4,26" fill="none" stroke="#aaa" stroke-width="3"/></svg>

<footer class="site-footer">
  <h4 style="left:99px">LINKS</h4>
  <ul class="footer-list" style="left:99px"><li>Home</li><li>About Us</li><li>Services</li><li>Our Team</li><li>Clients</li><li>Blog</li></ul>
  <div class="vrule" style="left:205px"></div>
  <h4 style="left:252px">JOIN OUR NEWSLETTER</h4>
  <p class="newsletter-copy">Excepteur sint occaecat cupidatat non proident, sunt in culpa qui</p>
  <div class="email-field">Enter Your Email</div>
  <div class="btn-subscribe">SUBSCRIBE</div>
  <div class="vrule" style="left:555px"></div>
  <h4 style="left:589px">INFORMATION</h4>
  <ul class="footer-list" style="left:589px"><li>Terms &amp; Conditions</li><li>Privacy policy</li><li>Disclaimer</li><li>Contact us</li><li>Sitemap</li></ul>
  <h4 style="left:786px">WHY US</h4>
  <ul class="footer-list" style="left:786px"><li>Customers</li><li>Team</li><li>FAQ</li><li>News</li><li>Others</li></ul>
  <h4 style="left:939px">CONTACT INFO</h4>
  <div class="contact-line" style="top:82px">218 Quarry Lane<br>PO Box 4410<br>Ashby, ID 83000</div>
  <div class="contact-line" style="top:155px"><svg width="11" height="11" viewBox="0 0 12 12" style="vertical-align:-1px;margin-right:8px"><path d="M2 1 L4.5 1 L5.5 4 L4 5 Q5 7.5 7 8 L8 6.5 L11 7.5 L11 10 Q6 12 2 6 Q0.5 3 2 1Z" fill="#fff"/></svg>(555) 010-2234</div>
  <div class="contact-line" style="top:182px"><svg width="12" height="9" viewBox="0 0 12 9" style="vertical-align:0;margin-right:8px"><rect width="12" height="9" fill="#fff"/><polyline points="0,0 6,5 12,0" fill="none" stroke="#1c2b50" stroke-width="1.2"/></svg>office@mandtelectric.example</div>
</footer>

<div class="bottom-bar">
  <div class="copy">&copy; 2017. M&amp;T Electric. All rights reserved</div>
  <div class="social">Connect with our social network : <b>Plaza</b><b>Chirpa</b><b>Orbly</b><b>Pindle</b><b>Worknet</b></div>
</div>

</body>
</html>
```